Lantern Petals Website v.1 - attract floral shop franchisees

I need a simple information website for my new business. We are a franchisor of flower shops. The overall purpose of the website is to promote the company and the service, especially to potential franchisees and retailers. Only about 4 pages are required including homepage, About, For Supermarkets, For Franchisees, and Contact. No special functions are required except the site will have two separate inquiry forms that must be filled out online and submitted via automated email. Similarly, an email form should be linked from the Contact page. I have a logo and business cards designed by ArtMingle, and I would like the site to have a consistent color scheme and style. The key to design will be to express the joy and love associated with flowers and floral bouquets.
IMPORTANT - I will be exporting the website design to Wordpress CMS in a site hosted by HostNimbus. For smooth integration into WordPress hosted by HostNimbus, the designer should build the site using a WordPress-friendly format. Ideally, they should use HTML, CSS, and PHP. Creating a custom theme or using a page builder that exports to WordPress-compatible files is best. This ensures the site can be easily imported and managed within WordPress.

Target Market(s)

Potential franchisees (existing florists or creative types who might like to own a floral business) and supermarkets who might want us to run their floral department

Industry/Entity Type

Floral retailing

Requirements
Must have
• A brand theme that is beautiful, consistent throughout and builds on the logo design
Nice to have
• Show gender and ethnic diversity in customers and florists. Pictures of happy florists (for franchisees) and pictures of amazing floral department displays (for supermarkets)

```html
<!DOCTYPE html>
<html lang="en">
<head>
<meta charset="utf-8">
<title>Lantern Petals</title>
<link href="https://fonts.googleapis.com/css2?family=Great+Vibes&family=Montserrat:wght@400;500;600;700&display=swap" rel="stylesheet">
<style>
:root{
  --green:#1f8f42;
  --green-dark:#187a37;
  --orange:#f0a024;
  --ink:#222;
  --white:#fff;
  --header-bg:#f6fbf5;
}
*{margin:0;padding:0;box-sizing:border-box}
html,body{width:1200px;height:4004px;overflow:hidden;background:var(--white)}
body{position:relative;font-family:"Montserrat",sans-serif;color:var(--ink)}
.abs{position:absolute}
.script{font-family:"Great Vibes",cursive;font-weight:400}
.btn{position:absolute;display:flex;align-items:center;justify-content:center;border-radius:30px;font-weight:700;font-size:15px;color:var(--white);background:var(--orange)}
.btn.green{background:var(--green)}
.photo{position:absolute}

/* header */
.site-header{position:absolute;left:0;top:0;width:1200px;height:128px;background:var(--header-bg)}
.contact-chip{position:absolute;top:12px;display:flex;align-items:center;gap:14px;font-size:14px;padding-bottom:12px;border-bottom:1.5px solid var(--orange)}
.contact-chip svg{width:34px;height:34px}
.nav a{position:absolute;top:84px;font-size:13px;letter-spacing:.5px;color:var(--ink);text-decoration:none}
.brand{position:absolute;display:flex;align-items:center;gap:10px}
.brand .dot{width:30px;height:30px;border-radius:50%;background:var(--orange)}
.brand .name{font-family:"Montserrat",sans-serif;font-weight:600;color:var(--orange);font-size:26px;letter-spacing:.5px}

/* hero */
.hero-photo{left:0;top:128px;width:1200px;height:590px;background:radial-gradient(circle at 25% 40%,#8a6a2a,#3c3a24 45%,#2a3324 75%),#33311f}
.hero-shade{position:absolute;left:0;top:128px;width:1200px;height:590px;background:rgba(20,20,10,.35)}
.hero-text{position:absolute;left:0;width:1200px;text-align:center;color:var(--white)}

.section-title{position:absolute;left:0;width:1200px;text-align:center;color:var(--orange);font-size:66px}

/* offer cards */
.card{position:absolute;top:890px;width:455px;height:448px;border-radius:6px;overflow:hidden;color:var(--white);text-align:center}
.card.green{background:var(--green)}
.card.orange{background:var(--orange)}
.card h3{margin-top:42px;font-size:24px;font-weight:700}
.card p{margin:22px auto 0;width:380px;font-size:14px;line-height:28.5px}
.card .photo{left:0;top:230px;width:455px;height:218px}

.band-green{position:absolute;left:0;width:1200px;background:var(--green)}
.about-text{position:absolute;left:609px;top:1700px;width:450px;color:var(--white);font-size:14px;line-height:29.2px}

.gallery .photo{border-radius:3px}

.contact-text{position:absolute;left:0;width:1200px;text-align:center;color:var(--white);font-size:15px}

.footer-links a{position:absolute;top:3898px;font-size:14px;color:var(--ink);text-decoration:none}
.social{position:absolute;top:3822px;width:42px;height:42px;border-radius:50%;border:2px solid var(--orange)}
</style>
</head>
<body>

<header class="site-header">
  <div class="contact-chip" style="left:112px;width:252px">
    <svg viewBox="0 0 34 34"><circle cx="17" cy="17" r="15" fill="none" stroke="#222" stroke-width="2"/><rect x="9" y="11" width="16" height="12" rx="1.5" fill="#222"/><path d="M9 12l8 6 8-6" stroke="#fff" stroke-width="1.5" fill="none"/></svg>
    <span>hello@lantern-petals.com</span>
  </div>
  <div class="contact-chip" style="left:914px;width:172px">
    <svg viewBox="0 0 34 34"><circle cx="17" cy="17" r="15" fill="none" stroke="#222" stroke-width="2"/><path d="M11 10c1-1 2-1 3 0l2 3c.5 1 0 2-1 2.5 1 2 2.5 3.5 4.5 4.5.5-1 1.5-1.5 2.5-1l3 2c1 1 1 2 0 3-2 2-5 1.5-8-1s-5-6-6-8.5c-.5-2 0-3.5 0-4.5z" fill="#222"/></svg>
    <span style="font-size:13px">+1 555 014 2087</span>
  </div>
  <nav class="nav">
    <a href="#" style="left:146px">HOME</a>
    <a href="#" style="left:231px">ABOUT</a>
    <a href="#" style="left:326px">SUPERMARKETS</a>
    <a href="#" style="left:784px">FRANCHISEES</a>
    <a href="#" style="left:925px">CONTACT</a>
  </nav>
  <div class="brand" style="left:478px;top:44px">
    <span class="dot"></span><span class="name">Lantern Petals</span>
  </div>
</header>

<section class="hero">
  <div class="photo hero-photo" role="img" aria-label="Market stall filled with colourful bouquets of roses, gerberas and sunflowers"></div>
  <div class="hero-shade"></div>
  <div class="hero-text script" style="top:232px;font-size:44px">Welcome To</div>
  <div class="hero-text script" style="top:282px;font-size:84px">Lantern Petals</div>
  <div class="hero-text" style="top:394px;font-size:19px;font-weight:500">Lorem Ipsum is simply dummy text of the printing and typesetting</div>
  <div class="btn" style="left:514px;top:455px;width:168px;height:47px">Get Started</div>
  <svg class="abs" style="left:0;top:620px" width="1200" height="110" viewBox="0 0 1200 110" preserveAspectRatio="none">
    <path d="M0 62 C300 20 700 -10 1200 90 L1200 110 L0 110Z" fill="var(--orange)"/>
    <path d="M0 80 C300 38 700 10 1200 110 L0 110Z" fill="#fff"/>
  </svg>
</section>

<section class="offer">
  <h2 class="section-title script" style="top:760px">What We offer</h2>
  <article class="card green" style="left:112px">
    <h3>Supermarkets</h3>
    <p>Lantern Petals works with some of the country's largest and most progressive supermarkets to provide franchisee ownership and operation of</p>
    <div class="photo" role="img" aria-label="Supermarket floral department display with buckets of flowers" style="background:linear-gradient(180deg,#6f8a6a,#8a6f4a 60%,#5a4a34)"></div>
    <div class="btn" style="left:141px;top:185px;width:168px;height:45px">Read More</div>
  </article>
  <article class="card orange" style="left:634px">
    <h3>Franchisees</h3>
    <p>Lantern Petals brings the best of professional florists and supermarkets together for the benefit of consumers. It supports a national network of</p>
    <div class="photo" role="img" aria-label="Smiling florist arranging flowers in her shop" style="background:linear-gradient(180deg,#9a5a2a,#6a3a22 55%,#8a4a2a)"></div>
    <div class="btn green" style="left:141px;top:185px;width:168px;height:45px">Read More</div>
  </article>
</section>

<section class="about">
  <svg class="abs" style="left:0;top:1450px" width="1200" height="780" viewBox="0 0 1200 780" preserveAspectRatio="none">
    <path d="M0 10 C250 90 700 60 1200 10 L1200 660 C800 610 300 640 0 745Z" fill="var(--green)"/>
    <path d="M0 10 C250 90 700 60 1200 10 L1200 20 C700 72 250 100 0 30Z" fill="var(--orange)"/>
    <path d="M0 745 C300 640 800 610 1200 660 L1200 745 C800 620 300 650 0 755Z" fill="var(--orange)"/>
  </svg>
  <div class="abs" style="left:117px;top:1612px;width:423px;height:388px;background:var(--orange)"></div>
  <div class="photo" role="img" aria-label="Flower shop display with zinc buckets of pink, red and yellow blooms" style="left:180px;top:1672px;width:398px;height:361px;border-radius:3px;background:linear-gradient(160deg,#7a7a6a,#c24a6a 45%,#d8b84a 70%,#8a8a8a)"></div>
  <h2 class="abs script" style="left:610px;top:1600px;font-size:66px;color:var(--white)">About Us</h2>
  <p class="about-text">Fresh flowers convey beauty and love, and in our view should become something every person regularly enjoys. Lantern Petals is an entrepreneurial company created to make top quality fresh flowers and professionally-designed bouquets accessible to every consumer at affordable prices. Professional florists typically sell the finest quality stems, design the most beautiful bouquets and provide the finest customer service, but their costs – of floral products, retail spaces, labor and marketing – force them to pass high prices</p>
  <div class="btn" style="left:608px;top:1990px;width:174px;height:46px">Read More</div>
</section>

<section class="gallery">
  <h2 class="section-title script" style="top:2265px">Our Gallery</h2>
  <div class="photo" role="img" aria-label="Florist in apron tying a bouquet" style="left:0;top:2386px;width:185px;height:313px;background:linear-gradient(160deg,#b83a3a,#4a6aa0 55%,#8a5a3a)"></div>
  <div class="photo" role="img" aria-label="Florist arranging pink roses" style="left:0;top:2717px;width:188px;height:191px;background:linear-gradient(160deg,#d8a070,#d24a7a 60%,#5a7a4a)"></div>
  <div class="photo" role="img" aria-label="Florist standing in front of her flower shop" style="left:203px;top:2414px;width:404px;height:424px;background:linear-gradient(120deg,#4a6a8a,#5a3a2a 40%,#d8b04a 70%,#c25a7a)"></div>
  <div class="photo" role="img" aria-label="Large wrapped bouquet of mixed flowers" style="left:616px;top:2460px;width:405px;height:469px;background:linear-gradient(170deg,#6a6a6a,#a8a0a8 40%,#a05a7a 70%,#6a5a7a)"></div>
  <div class="photo" role="img" aria-label="Florist arranging a white bouquet at a counter" style="left:1040px;top:2386px;width:160px;height:194px;background:linear-gradient(160deg,#8a6a5a,#4a5a8a 55%,#d8d0c0)"></div>
  <div class="photo" role="img" aria-label="Florists working with potted plants and flowers" style="left:1040px;top:2592px;width:160px;height:312px;background:linear-gradient(160deg,#3a5a3a,#6a4a3a 50%,#d8a040)"></div>
</section>

<section class="contact">
  <svg class="abs" style="left:0;top:3065px" width="1200" height="590" viewBox="0 0 1200 590" preserveAspectRatio="none">
    <path d="M0 10 C250 90 700 70 1200 10 L1200 500 C800 470 300 480 0 575Z" fill="var(--green)"/>
    <path d="M0 10 C250 90 700 70 1200 10 L1200 20 C700 82 250 100 0 30Z" fill="var(--orange)"/>
    <path d="M0 575 C300 480 800 470 1200 500 L1200 520 C800 480 300 495 0 585Z" fill="var(--orange)"/>
  </svg>
  <h2 class="section-title script" style="top:3222px;color:var(--white)">Contact Us</h2>
  <p class="contact-text" style="top:3327px">Lorem Ipsum is simply dummy text of the printing and typesetting industry. Lorem Ipsum has been</p>
  <p class="contact-text" style="top:3356px;font-weight:700">Mail Us On hello@lantern-petals.com Or Call Us +1555 014 2087</p>
  <div class="btn" style="left:284px;top:3418px;width:287px;height:46px">New Florist Franchise Inquiry</div>
  <div class="btn" style="left:622px;top:3418px;width:286px;height:46px">Professional Florist Franchise</div>
</section>

<footer>
  <div class="brand" style="left:478px;top:3735px">
    <span class="dot"></span><span class="name">Lantern Petals</span>
  </div>
  <span class="social" style="left:514px" aria-label="Social profile"></span>
  <span class="social" style="left:577px" aria-label="Social profile"></span>
  <span class="social" style="left:639px" aria-label="Social profile"></span>
  <nav class="footer-links">
    <a href="#" style="left:362px">About</a>
    <a href="#" style="left:451px">For Supermarkets</a>
    <a href="#" style="left:625px">For Franchisees</a>
    <a href="#" style="left:782px">Contact</a>
  </nav>
  <div class="abs" style="left:113px;top:3950px;width:978px;height:2px;background:#222"></div>
  <p class="abs" style="left:0;top:3970px;width:1200px;text-align:center;font-size:13px">2024 Copyright © Lantern Petals | All Rights Reserved</p>
</footer>

</body>
</html>
```